Re-design and craft the perfect CV platform

We are building a CV-based platform designed to connect employees and employers, with a strong focus on individual users. As we're just starting out, we're looking to have our platform and logo redesigned to better reflect our vision
https://app.zelvorhire.com/
Colors like in the logo attached
#87C032 #6A6E71 #618930 - also you can add more colors if you like.
https://app.zelvorhire.com/dashboard - This page would be nice if you plan it, like personal Bio dashboard. Attached picture (Dashboard wanted) one idea from how we would like to be, but we are open for new professional ideas/solutions.
https://app.zelvorhire.com/posts - On this page we want to be showed the jobs posted. Attached one picture about our idea (jobs page wanted)
https://app.zelvorhire.com/profile - design something nice.
Only Photoshop, Illustrator or Figma
Other pictures from the app attached (as looking right now)

Target Market(s)

Job seekers, HR, Recruiters

Industry/Entity Type

HR Tech

Number of Pages Required

5+ page

Colors
00AB8E
00BBA5
67D7C9
C6EFE9
E9F9F6

```html
<!DOCTYPE html>
<html lang="en">
<head>
<meta charset="utf-8">
<title>HIREVERA – Empowering careers, one CV at a time</title>
<link href="https://fonts.googleapis.com/css2?family=Josefin+Sans:wght@400;600;700&family=Poppins:wght@400;500;600&display=swap" rel="stylesheet">
<style>
:root{
  --green:#87C032;
  --green-dark:#618930;
  --grey:#6A6E71;
  --ink:#1f1f1f;
  --pale:#eef6e4;
  --footer:#3b3b3b;
  --footer-dark:#2c2c2c;
  --white:#fff;
}
*{box-sizing:border-box;margin:0;padding:0}
html,body{width:1200px;height:3920px;overflow:hidden}
body{position:relative;font-family:"Poppins",sans-serif;color:var(--ink);background:var(--white)}
.abs{position:absolute}
.heading{font-family:"Josefin Sans",sans-serif;font-weight:600;text-transform:uppercase}
.btn{position:absolute;background:var(--green);color:#fff;font-family:"Josefin Sans",sans-serif;font-weight:600;font-size:15px;display:flex;align-items:center;justify-content:center;border-radius:3px;text-transform:uppercase}
.photo{position:absolute;border-radius:22px}

/* header */
.site-header{position:absolute;top:0;left:0;width:1200px;height:78px;background:#fff}
.logo-tab{position:absolute;left:100px;top:0;width:153px;height:107px;background:#fff;border-radius:0 0 16px 16px;box-shadow:0 3px 10px rgba(0,0,0,.06);display:flex;align-items:center;justify-content:center;gap:8px;z-index:3}
.logo-dot{width:16px;height:16px;border-radius:50%;background:var(--green)}
.logo-name{font-family:"Josefin Sans",sans-serif;font-weight:700;font-size:21px;color:var(--green)}
.nav{position:absolute;top:33px;font-family:"Josefin Sans",sans-serif;font-size:14px;color:#333;text-transform:uppercase}
.nav.active{color:var(--green)}

/* hero */
.hero{position:absolute;top:78px;left:0;width:1200px;height:450px;background:linear-gradient(120deg,#eef6e4 0%,#f6faf0 50%,#e8f2dd 100%)}
.hero-title{left:110px;top:106px;font-size:28px;color:var(--green)}
.hero-sub{left:110px;top:152px;font-size:25px;color:var(--ink)}
.hero-text{left:110px;top:196px;width:500px;font-size:14.5px;line-height:34.5px;color:#222}
.brand-tile{position:absolute;left:771px;top:225px;width:180px;height:182px;background:var(--green);border-radius:24px;display:flex;align-items:center;justify-content:center;font-family:"Josefin Sans",sans-serif;font-weight:700;font-size:28px;color:#fff;box-shadow:0 8px 20px rgba(0,0,0,.12)}

/* dashboard band */
.band{position:absolute;top:528px;left:0;width:1200px;height:452px;background:var(--green)}
.band-title{width:1200px;text-align:center;font-size:27px;color:#fff}
.mock-frame{position:absolute;left:164px;top:702px;width:870px;height:500px;background:#f1f7e9;border-radius:60px}
.mock{position:absolute;left:180px;top:712px;width:836px;height:472px;background:#fff;border-radius:50px 50px 40px 40px;overflow:hidden;font-size:8px;color:#444}
.mock-bar{position:absolute;top:0;left:0;width:100%;height:30px;background:#fff;border-bottom:10px solid #ececec}
.mock-tab{position:absolute;top:10px;font-size:7.5px;color:#555}
.mock-field{position:absolute;left:28px;width:124px;height:18px;border:1px solid #d8d8d8;border-radius:3px}
.mock-label{position:absolute;left:33px;font-size:7.5px;color:#444}
.social{position:absolute;border-radius:50%;background:#2b2b2b;border:4px solid #d9d9d9;box-shadow:0 4px 10px rgba(0,0,0,.25)}
.social span{position:absolute;inset:30%;border-radius:50%;background:#fff;opacity:.85}

/* how it works */
.rule{position:absolute;height:5px;width:58px;background:var(--green);border-radius:2px}
.section-title{position:absolute;width:1200px;text-align:center;font-size:31px;color:var(--ink)}
.section-title em{font-style:normal;color:var(--green)}
.step{position:absolute;top:1335px;width:288px;height:192px;background:#fff;border:1px solid #eee;box-shadow:0 2px 8px rgba(0,0,0,.06);border-radius:4px}
.step.active{background:var(--green);border-color:var(--green)}
.step-icon{position:absolute;left:30px;top:44px;width:62px;height:62px;border-radius:50%;background:var(--green);display:flex;align-items:center;justify-content:center}
.step.active .step-icon{background:#fff;top:26px;left:26px}
.step-label{position:absolute;left:30px;font-family:"Josefin Sans",sans-serif;font-size:17px;line-height:35px;text-transform:uppercase;color:#222}
.step.active .step-label{color:#fff;left:26px}

/* about */
.about-back{position:absolute;left:111px;top:1612px;width:432px;height:412px;background:var(--green);border-radius:14px}
.about-title{left:601px;top:1598px;font-size:31px}
.about-text{left:601px;top:1654px;width:480px;font-size:14.5px;line-height:34.3px;color:#222}

/* features */
.features{position:absolute;top:2099px;left:0;width:1200px;height:808px;background:var(--green)}
.feature{position:absolute;background:#fff;border-radius:8px}
.f-icon{position:absolute;width:62px;height:62px;border-radius:50%;background:#eef3e8;display:flex;align-items:center;justify-content:center}
.f-title{position:absolute;font-family:"Josefin Sans",sans-serif;font-weight:600;font-size:18px;color:var(--green);text-transform:uppercase;white-space:nowrap}
.f-text{position:absolute;font-size:15px;line-height:28px;color:#222;width:260px}
.f-link{position:absolute;font-family:"Josefin Sans",sans-serif;font-weight:600;font-size:18px;color:var(--green);text-decoration:underline}

/* news */
.news{position:absolute;top:3085px;width:269px}
.news-img{width:269px;height:167px;border-radius:10px}
.news-date{position:absolute;top:201px;font-family:"Josefin Sans",sans-serif;font-size:14px;color:var(--green)}
.news-cat{position:absolute;top:238px;font-family:"Josefin Sans",sans-serif;font-size:14px;color:#111}
.news-text{position:absolute;top:264px;width:250px;font-size:12.5px;line-height:27.4px;color:#333}
.news-line{position:absolute;right:0;top:198px;width:2px;height:222px;background:var(--green)}
.news .btn{top:389px;left:3px;width:100px;height:31px;font-size:13px}
.arrow{position:absolute;width:17px;height:17px;border-radius:50%;display:flex;align-items:center;justify-content:center}

/* footer */
.footer{position:absolute;top:3582px;left:0;width:1200px;height:274px;background:var(--footer)}
.footer-base{position:absolute;top:3856px;left:0;width:1200px;height:64px;background:var(--footer-dark);color:#fff;font-size:11px;display:flex;align-items:center;justify-content:center}
.footer-base b{color:var(--green);font-weight:400;margin:0 3px}
.f-col-title{position:absolute;top:3630px;font-family:"Josefin Sans",sans-serif;font-size:19px;color:var(--green)}
.f-col{position:absolute;top:3670px;font-size:11.5px;line-height:31.2px;color:#fff;text-transform:uppercase}
</style>
</head>
<body>

<!-- header -->
<header class="site-header">
  <div class="logo-tab"><span class="logo-dot"></span><span class="logo-name">HIREVERA</span></div>
  <span class="nav active" style="left:495px">Home</span>
  <span class="nav" style="left:578px">Features</span>
  <span class="nav" style="left:692px">About Us</span>
  <span class="nav" style="left:806px">Blog</span>
  <span class="nav" style="left:886px">Contact Us</span>
  <span class="btn" style="left:1010px;top:26px;width:78px;height:31px;font-size:13px">Sign Up</span>
</header>

<!-- hero -->
<section class="hero">
  <h1 class="abs heading hero-title" style="font-weight:400">Empowering Careers,</h1>
  <h2 class="abs heading hero-sub" style="font-weight:400">One CV at a time</h2>
  <p class="abs hero-text">Lorem ipsum dolor sit amet, consectetur adipiscing elit, sed do eiusmod tempor incididunt ut labore et dolore magna aliqua enim ad minim veniam.</p>
  <span class="btn" style="left:110px;top:320px;width:140px;height:40px">Browse Jobs</span>
</section>
<div class="photo" role="img" aria-label="Photo of a person typing on a laptop" style="left:666px;top:114px;width:146px;height:148px;background:linear-gradient(135deg,#8a7a6c,#d8d2cb)"></div>
<div class="photo" role="img" aria-label="Illustration of a magnifier over a group of candidates" style="left:929px;top:188px;width:122px;height:124px;background:linear-gradient(135deg,#9fd0cd,#c7e5e2)"></div>
<div class="photo" role="img" aria-label="Photo of a hand holding a magnifying glass" style="left:700px;top:344px;width:147px;height:148px;background:linear-gradient(135deg,#7fb6d8,#b8dbee)"></div>
<div class="photo" role="img" aria-label="Photo of a smiling candidate in an interview" style="left:964px;top:368px;width:122px;height:123px;background:linear-gradient(135deg,#6b4c3c,#d9d3cc)"></div>
<div class="brand-tile">HIREVERA</div>

<!-- dashboard band -->
<section class="band">
  <h2 class="abs heading band-title" style="top:64px;font-weight:400">Find the right job or hire the right talent.</h2>
  <h2 class="abs heading band-title" style="top:111px;color:var(--ink);font-weight:400">Your CV, your future.</h2>
</section>
<div class="mock-frame"></div>
<div class="mock">
  <div class="mock-bar">
    <span class="mock-tab" style="left:55px">▦ Dashboard</span>
    <span class="mock-tab" style="left:150px">⚲ Cv</span>
    <span class="mock-tab" style="left:225px">▤ Job posts</span>
    <span class="mock-tab" style="left:742px;color:var(--green);font-weight:600">HIREVERA</span>
  </div>
  <div class="abs" style="left:28px;top:60px;font-size:9px;color:#2b7de9;font-weight:600">Account</div>
  <div class="abs" style="left:28px;top:77px;font-size:7px;color:#5ea0f0">Manage your account settings</div>
  <div class="abs" style="left:20px;top:128px;width:796px;height:18px;background:#fdf8e4;font-size:7px;color:#b08a20;padding:4px 10px">⚠ Please fill in a valid company identification number</div>
  <span class="mock-label" style="top:164px">Company name</span>
  <div class="mock-field" style="top:176px"></div>
  <div class="mock-field" style="top:216px"></div><span class="mock-label" style="top:221px">Email address</span>
  <div class="mock-field" style="top:258px;border-color:#e08585"></div><span class="mock-label" style="top:263px">Identification number</span>
  <div class="mock-field" style="top:301px"></div><span class="mock-label" style="top:306px">Registration number</span>
  <div class="mock-field" style="top:343px"></div><span class="mock-label" style="top:348px">Address</span>
  <span class="mock-label" style="top:376px">Select language</span>
  <div class="mock-field" style="top:387px;width:72px;font-size:7px;padding:3px 6px">▪ english ⌄</div>
  <div class="abs" style="left:28px;top:448px;width:48px;height:18px;background:#73c86a;color:#fff;font-size:7px;border-radius:3px;display:flex;align-items:center;justify-content:center">Save</div>
</div>
<div class="social" style="left:124px;top:798px;width:80px;height:80px"><span></span></div>
<div class="social" style="left:976px;top:873px;width:64px;height:64px;background:#333"><span></span></div>
<div class="social" style="left:99px;top:1036px;width:52px;height:52px"><span></span></div>
<div class="social" style="left:1061px;top:1023px;width:66px;height:66px"><span></span></div>

<!-- how it works -->
<div class="rule" style="left:571px;top:1237px"></div>
<h2 class="heading section-title" style="top:1254px;font-weight:400"><em>How it</em> works</h2>
<div class="step">
  <div class="step-icon"><svg width="30" height="30" viewBox="0 0 30 30" fill="none" stroke="#fff" stroke-width="1.6"><rect x="6" y="4" width="16" height="22" rx="1"/><path d="M10 10h8M10 14h8M10 18h5M24 8l-7 12"/></svg></div>
  <div class="step-label" style="top:124px">Create CV</div>
</div>
<div class="step active" style="left:456px">
  <div class="step-icon"><svg width="32" height="32" viewBox="0 0 32 32" fill="none" stroke="#618930" stroke-width="1.6"><rect x="4" y="5" width="24" height="20" rx="1"/><path d="M4 9h24"/><circle cx="15" cy="17" r="4"/><path d="M18 20l4 4"/></svg></div>
  <div class="step-label" style="top:106px">Browse opportunities/<br>post jobs</div>
</div>
<div class="step" style="left:757px">
  <div class="step-icon"><svg width="32" height="32" viewBox="0 0 32 32" fill="none" stroke="#fff" stroke-width="1.6"><circle cx="16" cy="9" r="4"/><path d="M9 20c1-4 4-6 7-6s6 2 7 6"/><rect x="7" y="20" width="18" height="8" rx="1"/></svg></div>
  <div class="step-label" style="top:106px">Match with employers/<br>candidates</div>
</div>
<div class="abs" style="left:154px;top:1335px"></div>

<!-- about -->
<div class="about-back"></div>
<div class="photo" role="img" aria-label="Photo of hands on a laptop with floating recruitment icons" style="left:120px;top:1604px;width:425px;height:412px;border-radius:14px;background:linear-gradient(135deg,#3a3a3a,#8d8d8d 60%,#c9c9c9)"></div>
<h2 class="abs heading about-title" style="font-weight:400"><span style="color:var(--green)">About</span> HIREVERA</h2>
<div class="rule" style="left:876px;top:1611px;height:4px"></div>
<p class="abs about-text">Lorem ipsum dolor sit amet, consectetur adipiscing elit, sed do eiusmod tempor incididunt ut labore et dolore magna aliqua. Ut enim ad minim veniam, quis nostrud exercitation ullamco laboris nisi ut aliquip ex ea commodo consequat. Duis aute irure dolor in reprehenderit in voluptate velit esse cillum dolore eu fugiat nulla pariatur. Excepteur sint occaecat cupidatat non proident.</p>
<p class="abs about-text" style="top:1870px">Lorem ipsum dolor sit amet, consectetur adipiscing elit, sed do eiusmod tempor incididunt ut labore et dolore magna aliqua.</p>
<span class="btn" style="left:601px;top:1977px;width:166px;height:40px">Create your CV</span>

<!-- features -->
<section class="features">
  <div class="rule" style="left:571px;top:50px;background:#fff"></div>
  <h2 class="heading section-title" style="top:70px;color:#222;font-weight:400"><em style="color:#fff">Our</em> features</h2>
</section>
<div class="feature" style="left:123px;top:2250px;width:297px;height:267px">
  <div class="f-icon" style="left:22px;top:24px"><svg width="32" height="32" viewBox="0 0 32 32" fill="none" stroke="#333" stroke-width="1.4"><rect x="7" y="4" width="18" height="24" rx="1"/><circle cx="16" cy="12" r="3"/><path d="M11 20h10M11 23h10"/></svg></div>
  <div class="f-title" style="left:22px;top:121px">Custom CV templates</div>
  <p class="f-text" style="left:22px;top:155px">Lorem ipsum dolor sit amet, consectetur adipiscing</p>
  <span class="f-link" style="left:22px;top:225px">Learn more</span>
</div>
<div class="feature" style="left:453px;top:2250px;width:624px;height:267px">
  <div class="f-icon" style="left:26px;top:24px"><svg width="32" height="32" viewBox="0 0 32 32" fill="none" stroke="#333" stroke-width="1.4"><circle cx="16" cy="15" r="6"/><path d="M20 19l6 6"/><circle cx="9" cy="8" r="2"/><circle cx="23" cy="8" r="2"/><circle cx="16" cy="6" r="2"/></svg></div>
  <div class="f-title" style="left:26px;top:121px">Smart job matching</div>
  <p class="f-text" style="left:26px;top:155px">Lorem ipsum dolor sit amet, consectetur adipiscing</p>
  <span class="f-link" style="left:26px;top:225px">Learn more</span>
  <div class="photo" role="img" aria-label="Photo of three colleagues reviewing documents at a window" style="left:283px;top:8px;width:333px;height:252px;border-radius:8px;background:linear-gradient(135deg,#4a6a74,#a7b4a8 50%,#d6b25a)"></div>
</div>
<div class="feature" style="left:123px;top:2549px;width:624px;height:288px">
  <div class="f-icon" style="left:27px;top:24px"><svg width="32" height="32" viewBox="0 0 32 32" fill="none" stroke="#333" stroke-width="1.4"><rect x="5" y="6" width="22" height="18" rx="1"/><path d="M9 20v-4M13 20v-7M17 20v-5M21 20v-9"/></svg></div>
  <div class="f-title" style="left:27px;top:122px">Employer dashboard</div>
  <p class="f-text" style="left:27px;top:156px">Lorem ipsum dolor sit amet, consectetur adipiscing</p>
  <span class="f-link" style="left:27px;top:226px">Learn more</span>
  <div class="photo" role="img" aria-label="Illustration of analytics charts on screens" style="left:283px;top:9px;width:333px;height:272px;border-radius:8px;background:linear-gradient(135deg,#1e3f7a,#3f7fc4 55%,#c9a24a)"></div>
</div>
<div class="feature" style="left:780px;top:2549px;width:297px;height:288px">
  <div class="f-icon" style="left:22px;top:24px"><svg width="32" height="32" viewBox="0 0 32 32" fill="none" stroke="#333" stroke-width="1.4"><rect x="5" y="6" width="20" height="16" rx="1"/><rect x="19" y="17" width="9" height="8" rx="1"/><path d="M21 17v-3a2.5 2.5 0 015 0v3"/></svg></div>
  <div class="f-title" style="left:22px;top:122px">Data security &amp; privacy</div>
  <p class="f-text" style="left:22px;top:159px">Lorem ipsum dolor sit amet, consectetur adipiscing</p>
  <span class="f-link" style="left:22px;top:239px">Learn more</span>
</div>

<!-- news -->
<div class="rule" style="left:571px;top:2984px"></div>
<h2 class="heading section-title" style="top:3008px;font-weight:400"><em>Latest</em> news &amp; blogs</h2>
<div class="arrow" style="left:112px;top:3160px;background:#111"><svg width="8" height="8" viewBox="0 0 8 8"><path d="M5 1L2 4l3 3" stroke="#fff" stroke-width="1.5" fill="none"/></svg></div>
<div class="arrow" style="left:1072px;top:3160px;background:var(--green)"><svg width="8" height="8" viewBox="0 0 8 8"><path d="M3 1l3 3-3 3" stroke="#fff" stroke-width="1.5" fill="none"/></svg></div>

<article class="news" style="left:157px">
  <div class="news-img" role="img" aria-label="Photo of two businessmen shaking hands" style="background:linear-gradient(135deg,#5f6a72,#b7c0c6)"></div>
  <span class="news-date">13 May 2024</span><span class="news-cat">Job Search</span>
  <p class="news-text">Lorem ipsum dolor sit amet, consectetur adipiscing elit, sed do eiusmod tempor incididunt ut labore et dolore magna aliqua.</p>
  <div class="news-line"></div><span class="btn">Read more</span>
</article>
<article class="news" style="left:467px">
  <div class="news-img" role="img" aria-label="Photo of a plant growing from a jar of coins" style="background:linear-gradient(135deg,#9bb4cc,#dbe6ee)"></div>
  <span class="news-date">18 August 2024</span><span class="news-cat">Career Growth</span>
  <p class="news-text">Lorem ipsum dolor sit amet, consectetur adipiscing elit, sed do eiusmod tempor incididunt ut labore et dolore magna aliqua.</p>
  <div class="news-line"></div><span class="btn">Read more</span>
</article>
<article class="news" style="left:776px">
  <div class="news-img" role="img" aria-label="Photo of two colleagues working at computer monitors" style="background:linear-gradient(135deg,#1f2a35,#5a6a78)"></div>
  <span class="news-date">22 June 2024</span><span class="news-cat">Industry News</span>
  <p class="news-text">Lorem ipsum dolor sit amet, consectetur adipiscing elit, sed do eiusmod tempor incididunt ut labore et dolore magna aliqua.</p>
  <div class="news-line"></div><span class="btn">Read more</span>
</article>

<!-- footer -->
<footer class="footer">
  <div class="abs" style="left:95px;top:90px;display:flex;align-items:center;gap:14px">
    <span style="width:30px;height:30px;border-radius:50%;background:var(--green)"></span>
    <span style="font-family:'Josefin Sans',sans-serif;font-weight:700;font-size:44px;color:var(--green)">HIREVERA</span>
  </div>
</footer>
<span class="f-col-title heading" style="left:451px;font-weight:400">Quick Links</span>
<div class="f-col" style="left:451px">Home<br>Features<br>About Us<br>Blog<br>Contact Us</div>
<span class="f-col-title heading" style="left:648px;font-weight:400">Other Links</span>
<div class="f-col" style="left:648px">Information<br>Privacy Policy<br>Terms of Use<br>Site Map<br>Help Center</div>
<span class="f-col-title heading" style="left:854px;font-weight:400">Newsletter</span>
<div class="abs" style="left:855px;top:3681px;width:249px;height:37px;border:1px solid #ddd;color:#fff;font-size:11px;display:flex;align-items:center;padding-left:14px">ENTER EMAIL ADDRESS</div>
<span class="btn" style="left:855px;top:3739px;width:128px;height:32px;font-size:12px">Subscribe Now</span>
<div class="footer-base">© 2024 <b>HIREVERA</b>. ALL RIGHTS RESERVED.</div>

</body>
</html>
```